Coffeeshop menu for filter tip

We want to have a cannabis (coffeeshop) menu in the size 25mm wide x 60mm wide. Some examples attached.

it must have the following text:
Menu

WEED p/g
Oblivane €16
Cloudplum €14
Tide Runner €14
Quincefig €16
Mega Marsh €14
Grey Heron €14

HASH p/g
Tashar Amber €12
Pebble Frost€11
Lime Dunes €14
Ash Petal €10

Target Market(s)

tourist in Amsterdam

Requirements
Nice to have
• cannabis sign leaf
• No Cigarettes allowed symbol

```html
<!DOCTYPE html>
<html lang="en">
<head>
<meta charset="utf-8">
<title>Menu</title>
<link rel="stylesheet" href="https://fonts.googleapis.com/css2?family=Berkshire+Swash&family=Bangers&family=Kaushan+Script&family=Lobster&family=Lobster+Two:wght@700&family=Permanent+Marker&family=Rubik+Wet+Paint&family=Rye&family=Sniglet:wght@800&family=UnifrakturMaguntia&family=Yellowtail&display=swap">
<style>
  :root {
    --leaf-green: #1f8f3c;
    --leaf-green-dark: #136b2a;
    --leaf-green-light: #34ad52;
    --heading-outline: #0c4f20;
    --panel-brown: #4b2a0e;
    --panel-red: #8d1c12;
    --panel-edge: #3a1f08;
    --ink-white: #ffffff;
  }
  * { margin: 0; padding: 0; box-sizing: border-box; }
  html, body { width: 1200px; height: 2880px; overflow: hidden; }
  body { position: relative; background: var(--leaf-green); }

  .menu-title {
    position: absolute; width: 1px; height: 1px; overflow: hidden;
    clip: rect(0 0 0 0); white-space: nowrap;
  }

  .leaf-pattern {
    position: absolute; inset: 0;
    background:
      radial-gradient(ellipse 260px 220px at 12% 4%, var(--leaf-green-light) 0, transparent 70%),
      radial-gradient(ellipse 260px 220px at 88% 4%, var(--leaf-green-light) 0, transparent 70%),
      radial-gradient(ellipse 300px 260px at 92% 56%, var(--leaf-green-light) 0, transparent 70%),
      radial-gradient(ellipse 300px 260px at 8% 60%, var(--leaf-green-light) 0, transparent 70%),
      radial-gradient(ellipse 300px 260px at 10% 99%, var(--leaf-green-light) 0, transparent 70%),
      radial-gradient(ellipse 300px 260px at 90% 99%, var(--leaf-green-light) 0, transparent 70%),
      linear-gradient(180deg, var(--leaf-green) 0%, var(--leaf-green-dark) 100%);
  }

  .menu-art { position: absolute; inset: 0; width: 1200px; height: 2880px; }

  .section-heading {
    font-family: "Permanent Marker", cursive;
    font-size: 230px;
    fill: var(--ink-white);
    stroke: var(--heading-outline);
    stroke-width: 22px;
    stroke-linejoin: round;
    paint-order: stroke fill;
  }

  .price-panel { fill: url(#panel-glow); stroke: var(--panel-edge); stroke-width: 10px; }

  .strain-name, .strain-price { fill: var(--ink-white); }
  .strain-price { font-family: "Rye", serif; font-size: 112px; }

  .strain--oblivane { font-family: "Rubik Wet Paint", cursive; font-size: 140px; }
  .strain--cloudplum { font-family: "Rye", serif; font-size: 122px; }
  .strain--tide-runner { font-family: "Bangers", cursive; font-size: 150px; }
  .strain--quincefig { font-family: "Lobster", cursive; font-size: 150px; }
  .strain--mega-marsh { font-family: "Berkshire Swash", cursive; font-size: 132px; }
  .strain--grey-heron { font-family: "Yellowtail", cursive; font-size: 150px; }
  .strain--tashar-amber { font-family: "Kaushan Script", cursive; font-size: 124px; }
  .strain--pebble-frost { font-family: "UnifrakturMaguntia", serif; font-size: 132px; }
  .strain--lime-dunes { font-family: "Lobster Two", cursive; font-weight: 700; font-size: 140px; }
  .strain--ash-petal { font-family: "Sniglet", sans-serif; font-weight: 800; font-size: 130px; }
</style>
</head>
<body>
  <h1 class="menu-title">Menu</h1>
  <div class="leaf-pattern" role="img" aria-label="Repeating cannabis leaf pattern on green"></div>

  <svg class="menu-art" viewBox="0 0 1200 2880" xmlns="http://www.w3.org/2000/svg">
    <defs>
      <radialGradient id="panel-glow" cx="50%" cy="50%" r="60%">
        <stop offset="0" stop-color="#8d1c12"/>
        <stop offset="0.62" stop-color="#4b2a0e"/>
        <stop offset="1" stop-color="#3a1f08"/>
      </radialGradient>
    </defs>

    <text class="section-heading" x="50" y="320" textLength="1100" lengthAdjust="spacingAndGlyphs">WEED P/G</text>

    <g aria-label="Weed prices per gram">
      <rect class="price-panel" x="30" y="375" width="1140" height="1235" rx="90"/>
      <text class="strain-name strain--oblivane" x="70" y="545" textLength="720" lengthAdjust="spacingAndGlyphs">Oblivane</text>
      <text class="strain-price" x="1130" y="545" text-anchor="end" textLength="220" lengthAdjust="spacingAndGlyphs">€16</text>

      <text class="strain-name strain--cloudplum" x="70" y="735" textLength="760" lengthAdjust="spacingAndGlyphs">Cloudplum</text>
      <text class="strain-price" x="1130" y="735" text-anchor="end" textLength="220" lengthAdjust="spacingAndGlyphs">€14</text>

      <text class="strain-name strain--tide-runner" x="70" y="915" textLength="790" lengthAdjust="spacingAndGlyphs">TIDE RUNNER</text>
      <text class="strain-price" x="1130" y="915" text-anchor="end" textLength="220" lengthAdjust="spacingAndGlyphs">€14</text>

      <text class="strain-name strain--quincefig" x="70" y="1105" textLength="800" lengthAdjust="spacingAndGlyphs">Quincefig</text>
      <text class="strain-price" x="1130" y="1105" text-anchor="end" textLength="220" lengthAdjust="spacingAndGlyphs">€16</text>

      <text class="strain-name strain--mega-marsh" x="70" y="1300" textLength="780" lengthAdjust="spacingAndGlyphs">Mega Marsh</text>
      <text class="strain-price" x="1130" y="1300" text-anchor="end" textLength="220" lengthAdjust="spacingAndGlyphs">€14</text>

      <text class="strain-name strain--grey-heron" x="70" y="1495" textLength="790" lengthAdjust="spacingAndGlyphs">Grey Heron</text>
      <text class="strain-price" x="1130" y="1495" text-anchor="end" textLength="220" lengthAdjust="spacingAndGlyphs">€14</text>
    </g>

    <text class="section-heading" x="50" y="1880" textLength="1100" lengthAdjust="spacingAndGlyphs">HASH P/G</text>

    <g aria-label="Hash prices per gram">
      <rect class="price-panel" x="30" y="1925" width="1140" height="925" rx="90"/>
      <text class="strain-name strain--tashar-amber" x="70" y="2095" textLength="810" lengthAdjust="spacingAndGlyphs">Tashar Amber</text>
      <text class="strain-price" x="1130" y="2095" text-anchor="end" textLength="220" lengthAdjust="spacingAndGlyphs">€12</text>

      <text class="strain-name strain--pebble-frost" x="70" y="2300" textLength="810" lengthAdjust="spacingAndGlyphs">Pebble Frost</text>
      <text class="strain-price" x="1130" y="2300" text-anchor="end" textLength="220" lengthAdjust="spacingAndGlyphs">€11</text>

      <text class="strain-name strain--lime-dunes" x="70" y="2500" textLength="800" lengthAdjust="spacingAndGlyphs">Lime Dunes</text>
      <text class="strain-price" x="1130" y="2500" text-anchor="end" textLength="220" lengthAdjust="spacingAndGlyphs">€14</text>

      <text class="strain-name strain--ash-petal" x="70" y="2705" textLength="820" lengthAdjust="spacingAndGlyphs">Ash Petal</text>
      <text class="strain-price" x="1130" y="2705" text-anchor="end" textLength="220" lengthAdjust="spacingAndGlyphs">€10</text>
    </g>
  </svg>
</body>
</html>
```